Travel Agency Website - Simple General

Need a 7 page simple design that is pretty repetitive. Need to be able to load quickly that is SEO optimized. Trying to give ideas on what they can do, be personal as we are local, but at the same time come across as professional and get information easily with little burden.

- Landing Page
- Brimwell Vacations Page
- Family Trips
- Road Trips from Texas
- Other Destinations
- About Us Page
- Contact Us Page

Target Market(s)

Families

Coding

Coded - Design and coding required

Number of Pages Required

5+ page

Colors

Designer to choose colors to be used in the design.

Requirements
Must have
• Like it to flow easily with our logo. Use that for colors, etc.

```html
<!DOCTYPE html>
<html lang="en">
<head>
<meta charset="utf-8">
<title>Sunpath Travel Co. — Perfect Family Getaways</title>
<link rel="stylesheet" href="https://fonts.googleapis.com/css2?family=Outfit:wght@400;500;600;700&display=swap">
<style>
:root{
  --teal:#4f9294;
  --teal-dark:#1f5f63;
  --teal-line:#9fd0cc;
  --gold:#c49a4c;
  --gold-light:#d8b36a;
  --cream:#f8f3ec;
  --ink:#1f3d4a;
  --white:#ffffff;
  --sky-top:#3f86d2;
  --sky-mid:#8fbde8;
  --snow:#eef3f8;
}
*{box-sizing:border-box;margin:0;padding:0}
html,body{width:1200px;height:847px;overflow:hidden;background:var(--cream);font-family:"Outfit",sans-serif}
.page{position:relative;width:1200px;height:847px;overflow:hidden}
.hero-photo{position:absolute;left:0;top:0;width:1200px;height:786px;
  background:
   radial-gradient(ellipse 420px 380px at 880px 470px, rgba(214,74,150,.35), rgba(214,74,150,0) 70%),
   radial-gradient(ellipse 260px 240px at 760px 520px, rgba(30,110,160,.35), rgba(30,110,160,0) 70%),
   linear-gradient(180deg,var(--sky-top) 0%,var(--sky-mid) 45%,#dfe9f3 68%,var(--snow) 100%)}
.topbar{position:absolute;top:18px;left:82px;right:82px;display:flex;justify-content:space-between;color:var(--white);font-size:13.5px}
.topbar .item{display:flex;align-items:center;gap:9px}
.topbar .phone{font-size:15px;font-weight:500;margin-top:2px}
.icon-dot{width:28px;height:28px;border-radius:50%;background:var(--white);display:flex;align-items:center;justify-content:center}
.nav{position:absolute;left:49px;top:66px;width:1098px;height:60px;background:var(--cream);border-radius:30px;display:flex;align-items:center;padding:0 22px 0 30px}
.nav a{color:var(--ink);text-decoration:none;font-size:15.5px}
.nav .left{display:flex;align-items:center;gap:23px}
.nav .brand{flex:1;text-align:center;display:flex;align-items:center;justify-content:center;gap:8px;color:var(--teal-dark);font-weight:600;font-size:17px}
.brand .mark{width:14px;height:14px;border-radius:50%;background:var(--gold)}
.nav .right{display:flex;align-items:center;gap:36px}
.btn{display:inline-flex;align-items:center;gap:12px;background:var(--gold);color:var(--white);border-radius:22px;text-decoration:none}
.btn .arrow{width:28px;height:28px;border-radius:50%;background:var(--gold-light);display:flex;align-items:center;justify-content:center}
.nav .btn{height:38px;padding:0 6px 0 27px;color:var(--white);font-size:14.5px}
.promo{position:absolute;left:72px;top:208px;width:468px;height:420px}
.promo svg.frame{position:absolute;inset:0}
.promo-content{position:absolute;left:0;right:0;top:112px;text-align:center;color:var(--white)}
.promo h1{font-weight:700;font-size:39px;line-height:36px;letter-spacing:.3px}
.promo p{margin-top:16px;font-size:17px;line-height:19.5px}
.promo .btn{margin-top:24px;height:39px;padding:0 6px 0 24px;font-weight:600;font-size:13.5px;letter-spacing:.3px}
.footer{position:absolute;left:0;top:786px;width:1200px;height:61px;background:var(--cream);display:flex;align-items:center;justify-content:center;font-size:13.5px;color:var(--ink)}
.social{position:absolute;right:103px;top:19px;display:flex;gap:8px}
.social span{width:24px;height:24px;border-radius:50%;background:var(--teal-dark);display:block}
</style>
</head>
<body>
<div class="page">
  <div class="hero-photo" role="img" aria-label="Photo of a happy family of four in colorful ski gear posing on a snowy mountain top with skis, under a bright blue sky"></div>

  <div class="topbar">
    <div class="item">
      <span class="icon-dot"><svg width="16" height="12" viewBox="0 0 16 12"><rect x="1" y="1" width="14" height="10" rx="1.5" fill="none" stroke="#4f86c6" stroke-width="1.5"/><path d="M1.5 1.5 8 7l6.5-5.5" fill="none" stroke="#4f86c6" stroke-width="1.5"/></svg></span>
      hello@sunpathtravel.example
    </div>
    <div class="item phone">
      <span class="icon-dot"><svg width="14" height="14" viewBox="0 0 24 24"><path d="M6.6 10.8a15.2 15.2 0 0 0 6.6 6.6l2.2-2.2c.3-.3.7-.4 1-.2 1.1.4 2.3.6 3.6.6.6 0 1 .4 1 1V20c0 .6-.4 1-1 1A17 17 0 0 1 3 4c0-.6.4-1 1-1h3.5c.6 0 1 .4 1 1 0 1.3.2 2.5.6 3.6.1.3 0 .7-.2 1z" fill="#4f86c6"/></svg></span>
      Phone Number (555) 014 2290
    </div>
  </div>

  <nav class="nav">
    <div class="left">
      <a href="#" aria-label="Home"><svg width="14" height="13" viewBox="0 0 14 13"><path d="M7 0 0 6h2v7h4V9h2v4h4V6h2z" fill="#c49a4c"/></svg></a>
      <a href="#">Brimwell Vacations</a>
      <a href="#">Family Trips</a>
      <a href="#">Texas Road Trips</a>
    </div>
    <div class="brand"><span class="mark"></span>Sunpath Travel Co.</div>
    <div class="right">
      <a href="#">Other Destinations</a>
      <a href="#">About Us</a>
      <a class="btn" href="#">Contact Us <span class="arrow"><svg width="10" height="10" viewBox="0 0 10 10"><path d="M2 8 8 2M3.5 2H8v4.5" stroke="#fff" stroke-width="1.5" fill="none"/></svg></span></a>
    </div>
  </nav>

  <section class="promo">
    <svg class="frame" viewBox="0 0 468 420" width="468" height="420" aria-hidden="true">
      <path d="M234 4 C265 30 300 40 345 40 C400 40 410 80 430 96 C460 110 458 160 458 200 C458 250 470 240 460 270 C440 300 445 340 420 350 C390 360 380 385 330 385 C290 385 260 395 234 416 C208 395 178 385 138 385 C88 385 78 360 48 350 C23 340 28 300 8 270 C-2 240 10 250 10 200 C10 160 8 110 38 96 C58 80 68 40 123 40 C168 40 203 30 234 4Z" fill="#4f9294" fill-opacity=".95"/>
      <path d="M234 22 C262 44 296 54 340 54 C388 54 398 88 414 102 C440 114 442 160 442 200 C442 246 452 240 444 266 C428 292 430 330 408 338 C382 348 370 371 326 371 C290 371 260 380 234 398 C208 380 178 371 142 371 C98 371 86 348 60 338 C38 330 40 292 24 266 C16 240 26 246 26 200 C26 160 28 114 54 102 C70 88 80 54 128 54 C172 54 206 44 234 22Z" fill="none" stroke="#9fd0cc" stroke-width="1.5"/>
      <g fill="#fff">
        <path d="M236 48l4 16 15 4-15 4-4 16-4-16-15-4 15-4z"/>
        <path d="M196 70l2 8 8 2-8 2-2 8-2-8-8-2 8-2z"/>
        <path d="M276 70l2 7 7 2-7 2-2 7-2-7-7-2 7-2z"/>
        <path d="M408 190l3 12 12 3-12 3-3 12-3-12-12-3 12-3z"/>
        <path d="M110 266l2 10 10 2-10 2-2 10-2-10-10-2 10-2z"/>
      </g>
    </svg>
    <div class="promo-content">
      <h1>PERFECT FAMILY<br>GETAWAYS</h1>
      <p>tress-free, fun-filled vacations<br>designed for all ages—because every<br>family deserves time together.</p>
      <a class="btn" href="#">PLAN FAMILY TRIP <span class="arrow"><svg width="10" height="10" viewBox="0 0 10 10"><path d="M2 8 8 2M3.5 2H8v4.5" stroke="#fff" stroke-width="1.5" fill="none"/></svg></span></a>
    </div>
  </section>

  <footer class="footer">
    © 2026 Sunpath Travel Co. All Right Reserved
    <div class="social"><span aria-label="Social link"></span><span aria-label="Social link"></span></div>
  </footer>
</div>
</body>
</html>
```